Brightway Haus Inc. Business Card Design

Brightway Haus Inc. is in search of a great clean design for our business cards!

Looking to incorporate our full logo and watermark on side one (however, I am open to having the text and watermark separated within the design.)

On side two, I am looking to have contact information (Name, Position, Phone #, Email, Website (www.thebrightwayhaus.ca). Can have the logo and/or watermark as part of the design if applicable.

Please add tagline "Where Shine Counts" on either side 1 or 2. This tagline can be in a sans serif, serif or cursive font as long as it compliments overall design. Capitalization can be title or sentence case depending on how it fits within the design.

Get creative!! Looking for a clean, crisp, premium design! Looking for a glossy card finish with spot UV features when printed. Cards will also be printed with rounded corners. Standard dimensions (3.5 x 2).

Target Market(s)

B2B - primary clients are business owners or property management corporations. (residential jobs are few and far between)

Industry/Entity Type

Business

Contact Information for Business Card

- clean, crisp design
- double sided
- spot UV accents and glossy finish upon printing
- standard business card size (3.5 x 2) with rounded corners
- please see project description for requirements per side

Font styles to use
Sans Serif

Requirements
Must have
• - adequate bleeds with print ready files
• - cohesive design elements between side 1 & 2
• - spot UV elements (can be on both sides or just one, use your discretion)
• - colour pallet should match the logo file provided
• - incorporate tagline "where shine counts" (this tagline can be in a serif or sans serif font as long as it is complimentary to the overall design.
Nice to have
• - Premium elements with a clean design
Should not have
• - Please omit cartoon or whimsical like designs, think premium.
• - Colours should not stray from the pallet of the provided logo.

```html
<!DOCTYPE html>
<html lang="en">
<head>
<meta charset="utf-8">
<title>Brightway Haus Inc. Business Cards</title>
<link rel="stylesheet" href="https://fonts.googleapis.com/css2?family=Open+Sans:wght@400;600;700;800&family=Caveat:wght@500&display=swap">
<style>
  :root {
    --backdrop: #3b3b3c;
    --card-light: #f3f3f3;
    --card-dark-top: #1f2022;
    --card-dark-bottom: #141516;
    --teal: #19b5bd;
    --navy: #1f2a55;
    --text-grey: #4a4a4a;
    --divider: #c9c9c9;
    --silver: #e9e9e9;
  }
  * { box-sizing: border-box; margin: 0; padding: 0; }
  html, body {
    width: 1200px; height: 960px; overflow: hidden;
    background: var(--backdrop);
    font-family: "Open Sans", Arial, sans-serif;
  }
  .card {
    position: absolute;
    width: 600px; height: 342px;
    border-radius: 22px;
    overflow: hidden;
  }
  .card--front {
    left: 314px; top: 129px;
    background: var(--card-light);
  }
  .card--back {
    left: 311px; top: 488px;
    background: linear-gradient(170deg, var(--card-dark-top), var(--card-dark-bottom));
  }
  .brand {
    position: absolute;
    display: flex; align-items: center; gap: 7px;
    font-weight: 800;
    letter-spacing: -0.3px;
    white-space: nowrap;
  }
  .brand__square { display: block; flex: none; }
  .card--front .brand {
    left: 59px; top: 159px;
    font-size: 19px; line-height: 24px; color: var(--navy);
  }
  .card--front .brand__square { width: 22px; height: 22px; background: var(--teal); }
  .card--back .brand {
    left: 103px; top: 148px;
    font-size: 29px; line-height: 36px; color: var(--silver);
    gap: 9px;
  }
  .card--back .brand__square { width: 34px; height: 34px; background: var(--silver); }
  .divider {
    position: absolute; left: 337px; top: 81px;
    width: 1px; height: 192px; background: var(--divider);
  }
  .contact {
    position: absolute; left: 365px; top: 77px;
    color: var(--text-grey);
  }
  .contact__name { color: var(--teal); font-weight: 700; font-size: 20px; line-height: 24px; }
  .contact__role { color: var(--navy); font-weight: 700; font-size: 14px; line-height: 19px; }
  .contact__address { margin-top: 6px; font-size: 13px; line-height: 18px; }
  .contact__list { list-style: none; margin-top: 6px; font-size: 13px; }
  .contact__list li { display: flex; align-items: center; gap: 9px; height: 19.2px; white-space: nowrap; }
  .contact__list svg { width: 13px; height: 13px; fill: var(--teal); flex: none; }
  .tagline {
    position: absolute; left: 0; right: 0; top: 264px;
    text-align: center;
    font-family: "Caveat", cursive;
    font-size: 27px; color: #ffffff;
  }
</style>
</head>
<body>
  <section class="card card--front">
    <div class="brand"><span class="brand__square"></span>BRIGHTWAY HAUS INC.</div>
    <div class="divider"></div>
    <div class="contact">
      <p class="contact__name">ELENA MARSH</p>
      <p class="contact__role">CEO/FOUNDER</p>
      <p class="contact__address">2140 Harbour Crest Road<br>Halifax, Nova Scotia B3H 2Y9</p>
      <ul class="contact__list">
        <li><svg viewBox="0 0 16 16"><path d="M3 1l3 3-1.5 2a9 9 0 0 0 5.5 5.5L12 10l3 3-2 2C7 15 1 9 1 3z"/></svg>(902) 555-0148</li>
        <li><svg viewBox="0 0 16 16"><path d="M4 0h8v16H4zM5.5 2v10h5V2z"/></svg>(902) 555-0163</li>
        <li><svg viewBox="0 0 16 16"><path d="M4 1h8v4H4zM1 6h14v6h-3v3H4v-3H1zM5 10v4h6v-4z"/></svg>(902) 555-0192</li>
        <li><svg viewBox="0 0 16 16"><path d="M1 3h14v10H1zM2 4l6 5 6-5z" fill-rule="evenodd"/></svg>elena@thebrightwayhaus.ca</li>
        <li><svg viewBox="0 0 16 16"><circle cx="8" cy="8" r="7"/></svg>www.thebrightwayhaus.ca</li>
      </ul>
    </div>
  </section>

  <section class="card card--back">
    <div class="brand"><span class="brand__square"></span>BRIGHTWAY HAUS INC.</div>
    <p class="tagline">Where Shine Counts</p>
  </section>
</body>
</html>
```